MHFoster Consulting Limited

we are a company specialising in assisting New Zealand companies to venture into China on strategy, business development, M&A, and Governance.

Graphic Design

```html
<!DOCTYPE html>
<html lang="en">
<head>
<meta charset="utf-8">
<title>MHFoster Consulting Limited – Business Card</title>
<link rel="stylesheet" href="https://fonts.googleapis.com/css2?family=Cinzel:wght@400;700&display=swap">
<style>
  :root {
    --paper: #ffffff;
    --ink: #ffffff;
    --black: #000000;
    --crimson-deep: #7a0018;
    --crimson-bright: #e8002e;
    --panel-mid: #3a000c;
  }
  * { margin: 0; padding: 0; box-sizing: border-box; }
  html, body {
    width: 1200px;
    height: 800px;
    overflow: hidden;
    background: var(--paper);
  }
  .card {
    position: relative;
    width: 1200px;
    height: 800px;
    background: var(--paper);
    font-family: "Cinzel", serif;
    color: var(--ink);
  }
  .card__frame {
    position: absolute;
    left: 11px;
    top: 11px;
    width: 1177px;
    height: 778px;
    background: linear-gradient(160deg, var(--black) 0%, var(--crimson-deep) 65%, var(--crimson-bright) 100%);
  }
  .card__panel {
    position: absolute;
    left: 43px;
    top: 37px;
    width: 1113px;
    height: 721px;
    background: linear-gradient(155deg, var(--black) 0%, var(--panel-mid) 45%, var(--crimson-deep) 100%);
  }
  .company-name {
    position: absolute;
    top: 93px;
    left: 0;
    width: 100%;
    text-align: center;
    font-size: 29px;
    font-weight: 400;
    letter-spacing: 1px;
  }
  .person-name {
    position: absolute;
    top: 348px;
    left: 0;
    width: 100%;
    text-align: center;
    font-size: 44px;
    font-weight: 400;
    line-height: 1;
  }
  .divider {
    position: absolute;
    left: 134px;
    top: 396px;
    width: 930px;
    height: 2px;
    background: var(--ink);
  }
  .job-title {
    position: absolute;
    top: 402px;
    left: 0;
    width: 100%;
    text-align: center;
    font-size: 24px;
    font-weight: 700;
    letter-spacing: 1px;
    text-transform: lowercase;
  }
  .contact {
    position: absolute;
    left: 64px;
    top: 646px;
    list-style: none;
    font-size: 28px;
    line-height: 35px;
  }
</style>
</head>
<body>
  <div class="card">
    <div class="card__frame"></div>
    <div class="card__panel"></div>
    <p class="company-name">M H Foster Consulting Limited</p>
    <p class="person-name">Mei-Hua Foster</p>
    <div class="divider"></div>
    <p class="job-title">managing director</p>
    <ul class="contact">
      <li class="contact__phone">Phone: +64 21 555 0142</li>
      <li class="contact__skype">Skype:mhfosterconsulting</li>
      <li class="contact__email">email: mei-hua.foster@mhfosterconsulting.com</li>
    </ul>
  </div>
</body>
</html>
```